ASSET BASED PROGRAM FLIER

Need flier to market hard money loan products offered HARD MONEY FIX & FLIP PROGRAMS

We offer a variety of loan programs Some program highlights include......

1) No Minimum Credit Score
2) 3-5 Day Close
3) Up to 100% of Purchase & Rehab
4) Rates as Low as 7%
5) Loans Offered Nationwide

Contact us today for more information at (800) 416-9052 x23 or email us at mbelcourt@quillmarkfunding.com NMLS #318746 www.quillmarkfunding.com

Industry/Entity Type

Loan

```html
<!DOCTYPE html>
<html lang="en">
<head>
<meta charset="utf-8">
<title>Hard Money Fix &amp; Flip Programs – Quillmark Funding</title>
<link rel="stylesheet" href="https://fonts.googleapis.com/css2?family=Questrial&family=Lato:wght@400;700&display=swap">
<style>
  :root {
    --brand-blue: #1a63a3;
    --ink: #3a3a3a;
    --muted: #666;
    --white: #ffffff;
    --gold: #b59a3e;
    --title-box: rgba(70, 70, 70, 0.72);
    --frame: #f2f2f2;
  }
  * { box-sizing: border-box; margin: 0; padding: 0; }
  html, body { width: 922px; height: 1200px; overflow: hidden; background: var(--white); }
  .flier { position: relative; width: 922px; height: 1200px; overflow: hidden; background: var(--white); font-family: "Questrial", sans-serif; color: var(--ink); }

  .header { position: absolute; left: 0; top: 0; width: 922px; height: 138px; }
  .brand { position: absolute; left: 44px; top: 52px; display: flex; align-items: center; gap: 10px; font-size: 24px; color: var(--brand-blue); }
  .brand-mark { width: 22px; height: 22px; background: var(--gold); }
  .website { position: absolute; right: 40px; top: 60px; font-size: 18px; letter-spacing: 1px; color: var(--ink); text-decoration: none; }
  .website::after { content: ""; position: absolute; right: 0; bottom: -8px; width: 78px; height: 1px; background: #9a9a9a; }

  .hero-photo { position: absolute; left: 0; top: 138px; width: 922px; height: 573px;
    background: linear-gradient(160deg, #e9e4de 0%, #f3efea 35%, #d9d2cb 60%, #c8bdb4 80%, #f1f1f1 100%); }
  .title-box { position: absolute; left: 196px; top: 344px; width: 532px; height: 140px; background: var(--title-box);
    display: flex; align-items: center; justify-content: center; text-align: center; }
  .title-box h1 { font-weight: 400; font-size: 42px; line-height: 40px; color: var(--white); letter-spacing: -0.5px; }

  .feature-band { position: absolute; left: 0; top: 711px; width: 922px; height: 384px; background: var(--brand-blue); }

  .work-photo { position: absolute; top: 635px; width: 250px; height: 160px; border: 4px solid var(--frame); }
  .work-photo.p1 { left: 70px; background: linear-gradient(135deg, #c9b59a, #6e6a66 60%, #e6e2dc); }
  .work-photo.p2 { left: 340px; background: linear-gradient(135deg, #8e7a62, #4c6b93 55%, #c7b08a); }
  .work-photo.p3 { left: 610px; background: linear-gradient(135deg, #bfc3c6, #8a5a4a 55%, #d2c5b0); }

  .highlights { position: absolute; top: 852px; list-style: none; color: var(--white); font-size: 24px; line-height: 29px; }
  .highlights.col-1 { left: 94px; }
  .highlights.col-2 { left: 366px; }
  .highlights li { position: relative; padding-left: 30px; margin-bottom: 16px; }
  .highlights li svg { position: absolute; left: 0; top: 9px; width: 18px; height: 13px; }

  .spokesperson { position: absolute; left: 640px; top: 815px; width: 220px; height: 385px;
    border-radius: 110px 110px 0 0;
    background: linear-gradient(180deg, #8a5a3c 0%, #c99a7e 22%, #d9b39b 34%, #5a5f86 52%, #474c74 100%); }

  .contact { position: absolute; left: 76px; top: 1126px; font-family: "Lato", sans-serif; font-size: 16px; line-height: 21px; color: var(--muted); }
  .contact strong { color: var(--ink); font-weight: 700; }
  .contact svg { width: 16px; height: 12px; vertical-align: -1px; margin: 0 3px; }
  .nmls { position: absolute; left: 76px; top: 1173px; font-family: "Lato", sans-serif; font-size: 10px; color: var(--muted); }
</style>
</head>
<body>
<main class="flier">
  <header class="header">
    <div class="brand"><span class="brand-mark"></span>Quillmark Funding</div>
    <a class="website" href="#">www.quillmarkfunding.com</a>
  </header>

  <div class="hero-photo" role="img" aria-label="Close-up of a hand signing loan paperwork with a pen at a desk"></div>
  <div class="title-box"><h1>HARD MONEY FIX &amp;<br>FLIP PROGRAMS</h1></div>

  <section class="feature-band"></section>

  <div class="work-photo p1" role="img" aria-label="Investor and contractor reviewing plans in a renovated kitchen"></div>
  <div class="work-photo p2" role="img" aria-label="Contractor in a hard hat cutting wood"></div>
  <div class="work-photo p3" role="img" aria-label="Smiling builder carrying lumber on a job site"></div>

  <ul class="highlights col-1">
    <li><svg viewBox="0 0 19 14"><path d="M1 7 L7 12 L18 1" fill="none" stroke="#fff" stroke-width="2"/></svg>No Minimum<br>Credit Score</li>
    <li><svg viewBox="0 0 19 14"><path d="M1 7 L7 12 L18 1" fill="none" stroke="#fff" stroke-width="2"/></svg>3-5 Day<br>Close</li>
    <li><svg viewBox="0 0 19 14"><path d="M1 7 L7 12 L18 1" fill="none" stroke="#fff" stroke-width="2"/></svg>Up to 100% of<br>Purchase &amp; Rehab</li>
  </ul>
  <ul class="highlights col-2">
    <li><svg viewBox="0 0 19 14"><path d="M1 7 L7 12 L18 1" fill="none" stroke="#fff" stroke-width="2"/></svg>Rates as<br>Low as 7%</li>
    <li><svg viewBox="0 0 19 14"><path d="M1 7 L7 12 L18 1" fill="none" stroke="#fff" stroke-width="2"/></svg>Loans Offered<br>Nationwide</li>
  </ul>

  <div class="spokesperson" role="img" aria-label="Smiling loan officer giving two thumbs up"></div>

  <p class="contact">Contact us today for more information at
    <svg viewBox="0 0 16 12"><path d="M1 5 Q8 -1 15 5 L13 7 L11 5 L5 5 L3 7 Z M4 7 L12 7 L14 11 L2 11 Z" fill="#1a63a3"/></svg><strong>(800) 416-9052 x23</strong><br>
    or email us at
    <svg viewBox="0 0 16 12"><rect x="1" y="2" width="14" height="9" fill="#1a63a3"/><path d="M1 2 L8 7 L15 2" fill="none" stroke="#fff" stroke-width="1.2"/></svg><strong>mbelcourt@quillmarkfunding.com</strong>
  </p>
  <p class="nmls">NMLS #318746</p>
</main>
</body>
</html>
```